- Redesign our business card
- Logo remains unchanged
- Current business card attached

Target Market(s)

We are a property management company

Industry/Entity Type

Business

```html
<!DOCTYPE html>
<html lang="en">
<head>
<meta charset="utf-8">
<title>Harbourline Property Group – Business Card</title>
<link rel="stylesheet" href="https://fonts.googleapis.com/css2?family=Arimo:wght@400;700&family=Cardo&display=swap">
<style>
  :root {
    --page: #ffffff;
    --card: #ffffff;
    --card-edge: #d9d9d9;
    --brand: #7d7a58;
    --ink: #6b6b66;
    --ink-soft: #8c8c86;
    --label: #8c9a3a;
    --sand: #d9cfb0;
    --stone: #a7a48c;
    --olive: #a9a56c;
    --slate: #b4b5b8;
  }
  * { box-sizing: border-box; margin: 0; padding: 0; }
  html, body { width: 1200px; height: 900px; overflow: hidden; background: var(--page); }
  .canvas { position: relative; width: 1200px; height: 900px; font-family: "Arimo", Arial, sans-serif; }

  .card { position: absolute; background: var(--card); border: 1px solid var(--card-edge); overflow: hidden; }
  .card--front { left: 112px; top: 136px; width: 348px; height: 540px; }
  .card--back  { left: 590px; top: 250px; width: 548px; height: 346px; }

  .brand { position: absolute; z-index: 2; color: var(--brand); }
  .brand__name { display: flex; align-items: center; gap: 5px; font-weight: 700; font-size: 12px; letter-spacing: 0.01em; white-space: nowrap; }
  .brand__mark { width: 8px; height: 8px; background: var(--brand); }
  .brand__tagline { font-weight: 400; font-size: 8.5px; letter-spacing: 0.05em; margin-top: 2px; padding-left: 13px; color: var(--ink-soft); white-space: nowrap; }
  .card--front .brand { left: 76px; top: 110px; }
  .card--back .brand  { left: 40px; top: 108px; }

  .tones { position: absolute; z-index: 1; }
  .card--front .tones {
    left: 0; top: 160px; width: 100%; height: 320px;
    background:
      linear-gradient(180deg, rgba(255,255,255,1) 0%, rgba(255,255,255,0) 25%, rgba(255,255,255,0) 85%, rgba(255,255,255,1) 100%),
      linear-gradient(100deg, var(--slate) 0%, var(--stone) 35%, var(--sand) 60%, var(--olive) 100%);
  }
  .card--back .tones {
    left: 290px; top: 0; width: 258px; height: 100%;
    background:
      linear-gradient(90deg, rgba(255,255,255,1) 0%, rgba(255,255,255,0) 35%),
      linear-gradient(200deg, var(--sand) 0%, var(--stone) 45%, var(--olive) 70%, var(--slate) 100%);
  }

  .services { position: absolute; z-index: 2; left: 24px; bottom: 34px; font-size: 9px; color: var(--ink); white-space: nowrap; }

  .contact { position: absolute; z-index: 2; left: 40px; top: 206px; font-size: 9px; line-height: 14px; color: var(--ink); white-space: nowrap; }
  .contact__name { font-weight: 700; text-transform: uppercase; letter-spacing: 0.03em; }
  .contact__role { color: var(--ink-soft); margin-bottom: 10px; }
  .contact__address { margin-bottom: 6px; text-transform: uppercase; }
  .contact__key { font-weight: 700; color: var(--brand); }

  .label { position: absolute; top: 700px; font-family: "Cardo", Georgia, serif; font-size: 60px; color: var(--label); transform: translateX(-50%); }
  .label--front { left: 286px; }
  .label--back  { left: 846px; }
</style>
</head>
<body>
<main class="canvas">
  <section class="card card--front" aria-label="Card front">
    <div class="brand">
      <div class="brand__name"><span class="brand__mark"></span>HARBOURLINE PROPERTY GROUP</div>
      <div class="brand__tagline">STRATA MANAGEMENT SERVICES</div>
    </div>
    <div class="tones" role="img" aria-label="Layered translucent panels in sand, stone, olive and grey tones"></div>
    <p class="services">Strata Management | Community Management | Property Management</p>
  </section>

  <section class="card card--back" aria-label="Card back">
    <div class="brand">
      <div class="brand__name"><span class="brand__mark"></span>HARBOURLINE PROPERTY GROUP</div>
      <div class="brand__tagline">STRATA MANAGEMENT SERVICES</div>
    </div>
    <div class="contact">
      <p class="contact__name">Daniel Marsh</p>
      <p class="contact__role">Licensed Strata Manager</p>
      <p class="contact__address">PO Box 41, Eastwood Hills NSW 2031<br>12 Fenwick Lane Redfern NSW 2016</p>
      <p><span class="contact__key">T:</span> 02 9000 1234 <span class="contact__key">F:</span> 02 9000 5678 <span class="contact__key">M:</span> 0400 555 019</p>
      <p><span class="contact__key">E:</span> info@harbourlineproperty.com.au</p>
      <p><span class="contact__key">W:</span> www.harbourlineproperty.com.au</p>
    </div>
    <div class="tones" role="img" aria-label="Layered translucent panels in sand, stone, olive and grey tones"></div>
  </section>

  <p class="label label--front">front</p>
  <p class="label label--back">back</p>
</main>
</body>
</html>
```